Upscale business cards needed for Board of Directors

We need professional business cards created for members of our family business Board of Directors. We would like these relatively simple and straightforward, but also with a unique element to set them apart. Probably stick with neutral and simple colors - white, grey etc. We need space for the traditional elements, including name, title, address, email/phone number. And we will be creating several from this template so it needs to be template that is easy to switch information in and out of.
Business
See description

```html
<!DOCTYPE html>
<html lang="en">
<head>
<meta charset="utf-8">
<title>Halvard Holdings – Business Cards</title>
<link rel="stylesheet" href="https://fonts.googleapis.com/css2?family=Open+Sans:wght@400;700&display=swap">
<style>
  :root {
    --backdrop: #d6d6d6;
    --card: #333232;
    --brand-front: #a9a9a9;
    --brand-back: #ffffff;
    --gold: #b8a27c;
    --text-muted: #a3a3a3;
    --divider: #6d6c6b;
  }
  * { margin: 0; padding: 0; box-sizing: border-box; }
  html, body {
    width: 1200px; height: 1000px; overflow: hidden;
    background: var(--backdrop);
    font-family: "Open Sans", sans-serif;
  }
  .card {
    position: absolute;
    left: 287px; width: 626px; height: 358px;
    background: var(--card);
    box-shadow: 0 2px 6px rgba(0,0,0,0.25);
  }
  .card--front { top: 140px; }
  .card--back { top: 530px; }

  .brand-name {
    font-family: "Open Sans", sans-serif;
    font-weight: 700;
    text-transform: uppercase;
    line-height: 1;
    text-align: center;
  }
  .brand-name span { display: block; }

  .card--front .brand-name {
    position: absolute; left: 0; right: 0; top: 130px;
    color: var(--brand-front);
  }
  .card--front .brand-name .primary { font-size: 50px; letter-spacing: 1px; }
  .card--front .brand-name .secondary { font-size: 28px; letter-spacing: 11px; margin-top: 10px; }

  .front-website {
    position: absolute; left: 0; right: 0; top: 309px;
    text-align: center; font-size: 13px; color: var(--text-muted);
  }

  .card--back .brand-name {
    position: absolute; left: 38px; width: 252px; top: 150px;
    color: var(--brand-back);
  }
  .card--back .brand-name .primary { font-size: 35px; letter-spacing: 0.5px; }
  .card--back .brand-name .secondary { font-size: 19px; letter-spacing: 5px; margin-top: 6px; }

  .divider {
    position: absolute; left: 312px; top: 110px;
    width: 1px; height: 142px; background: var(--divider);
  }

  .contact {
    position: absolute; left: 338px; top: 106px;
    color: var(--text-muted); font-size: 13px; line-height: 18px;
  }
  .contact__name { color: var(--gold); font-weight: 700; font-size: 17px; line-height: 22px; }
  .contact__title { margin-bottom: 10px; }
  .contact__list { list-style: none; margin-bottom: 9px; }
  .contact__list li { display: flex; align-items: center; gap: 6px; }
  .contact__list svg { width: 10px; height: 10px; fill: var(--text-muted); flex: none; }
  .contact__address { font-style: normal; }
</style>
</head>
<body>

<section class="card card--front" aria-label="Card front">
  <h1 class="brand-name"><span class="primary">Halvard</span><span class="secondary">Holdings</span></h1>
  <p class="front-website">www.halvardholdings.com</p>
</section>

<section class="card card--back" aria-label="Card back">
  <h2 class="brand-name"><span class="primary">Halvard</span><span class="secondary">Holdings</span></h2>
  <div class="divider"></div>
  <div class="contact">
    <p class="contact__name">Daniel Marsh</p>
    <p class="contact__title">President</p>
    <ul class="contact__list">
      <li>
        <svg viewBox="0 0 10 10" aria-hidden="true"><path d="M2.5 0h5a1 1 0 0 1 1 1v8a1 1 0 0 1-1 1h-5a1 1 0 0 1-1-1V1a1 1 0 0 1 1-1zm0.5 1.5v6h4v-6zm2 6.7a0.6 0.6 0 1 0 0.01 0z"/></svg>
        012-555-0142
      </li>
      <li>
        <svg viewBox="0 0 10 10" aria-hidden="true"><path d="M0 2h10v6H0zm1 0.8v0.4l4 2.4 4-2.4v-0.4L5 5.2z"/></svg>
        info@halvardholdings.com
      </li>
      <li>
        <svg viewBox="0 0 10 10" aria-hidden="true"><circle cx="5" cy="5" r="4.5"/></svg>
        www.halvardholdings.com
      </li>
    </ul>
    <address class="contact__address">Street name, Suite 100 State,<br>Zip Code, Country</address>
  </div>
</section>

</body>
</html>
```